Website Design for Solar Panel Company

We are working with a company called VoltaNix.

Some sites to use for content/competitors and inspiration:
https://www.brivaloo.com
https://prod.aws-prod.kelmatrix.com
https://tovarqueworks.net
https://www.quorvex.com/solarpanels

Thank you for taking the time to consider designing a website for us. We are web developers based in Stockton, CA, USA. Most of our projects go through the same process. Understanding this process may help you win a project with us. We custom-code all of our websites in-house. We don’t have any requirements as to what tools you use for your design, but we prefer Figma files. For any design that we label as four-stars, we send it to the client for review. The client picks the final design they want us to use. Once we complete this process, we will continue to show additional clients all the four-star sites and purchase them later. Your designs will have multiple chances to sell. For better chances of success, we ask that you follow these guidelines.

IMAGES:
If you use any images or icons in the design, we ask that you have a link to the asset so we can purchase the image/icon. Most of the designs we submit do not have the customer’s images on them unless they have some great images. Be creative; show us the feeling you are trying to portray with your image choices. Use any royalty-free site you choose. We subscribe to Pendrel and mainly use their images, but we can purchase images outside of Pendrel. PLEASE NOTE: we will not submit designs to clients with watermarks on the images.

FONTS:
We ask that you identify the fonts used in the design. This can be done in a message if you want. We typically use Google Fonts and Pendrel Fonts.

CONTENT:
We're always open to different content and ideas. We often submit designs with stock images so the client can see our vision. We typically take pictures after the website launch to use their images with our vision. Lorem Ipsum is fine for paragraphs, but we ask that you write the headers in correct English. We want to be able to show the vision and identify the sections of the website.

INSPIRATION:
We typically add a couple of links in the brief of websites we like to help you get started in your design.

REVISIONS:
We do not often ask for revisions of the designs unless we see something in the design that may not appeal to the client. If there are slight changes that we want to make, we do that in the development process.

FEEDBACK:
We rarely give feedback on designs during the design process. We are working on many website projects and do not have the time to provide feedback. We usually respond if your request is well thought out and asks specific questions, but a note asking “feedback, please” usually goes unanswered.

```html
<!DOCTYPE html>
<html lang="en">
<head>
<meta charset="UTF-8">
<title>VoltaNix — Solar Energy</title>
<link href="https://fonts.googleapis.com/css2?family=Michroma&family=Mulish:wght@400;500;600;700&display=swap" rel="stylesheet">
<style>
:root{
  --green:#3cbf1e;
  --green-light:#5fe033;
  --green-dark:#1f8f14;
  --ink:#1a1a1a;
  --text:#333;
  --muted:#666;
  --card:#e7f1e2;
  --quote-bg:#e9ecef;
  --white:#fff;
  --black:#000;
}
*{box-sizing:border-box;margin:0;padding:0}
html,body{width:1200px;height:4098px;overflow:hidden}
body{position:relative;font-family:"Mulish",sans-serif;color:var(--text);background:var(--white)}
.abs{position:absolute}
.display{font-family:"Michroma",sans-serif;text-transform:uppercase;color:var(--ink);letter-spacing:.5px}
.btn{position:absolute;display:flex;align-items:center;justify-content:center;border-radius:30px;
  background:linear-gradient(90deg,var(--green-light),var(--green-dark));color:var(--white);
  font-family:"Michroma",sans-serif;font-size:12px;text-transform:uppercase}

/* top bar */
.topbar{top:0;left:0;width:1200px;height:60px;background:#f5f5f5;font-size:16px;color:#444}
.topbar .item{position:absolute;top:18px;display:flex;align-items:center;gap:10px}

/* nav */
.nav{top:60px;left:0;width:1200px;height:91px;background:var(--white)}
.brand{position:absolute;font-family:"Mulish",sans-serif;font-weight:700;color:var(--ink);letter-spacing:1px}
.nav .brand{left:111px;top:22px;font-size:38px}
.nav a{position:absolute;top:36px;font-size:15px;color:#333;text-decoration:none}

/* hero */
.hero{top:151px;left:0;width:1200px;height:600px;
  background:linear-gradient(100deg,#2f8a1c 0%,#3e7a2a 35%,#4a5b48 55%,#2b3034 80%,#3a4046 100%)}
.hero h1{position:absolute;left:111px;top:128px;width:520px;font-size:34px;line-height:48px;color:var(--white);font-weight:400}
.hero p{position:absolute;left:111px;top:228px;width:470px;font-size:15px;line-height:25px;color:var(--white)}

/* services */
.services h2{position:absolute;left:111px;top:843px;font-size:34px;font-weight:400}
.svc{position:absolute;top:928px;width:300px}
.svc h3{font-size:24px;font-weight:500;color:var(--ink);line-height:34px;margin-top:16px}
.svc p{font-size:12px;line-height:21px;color:#555;margin-top:12px;text-align:justify}
.divider{position:absolute;top:928px;width:1px;height:197px;background:#ddd}

/* about */
.about{top:1225px;left:0;width:1200px;height:556px;
  background:linear-gradient(100deg,#5e7da0 0%,#8aa0b8 30%,#c9b58c 60%,#e6a94a 80%,#d98a2a 100%)}
.about h2{position:absolute;left:610px;top:77px;font-size:34px;font-weight:400}
.about p{position:absolute;left:610px;top:133px;width:478px;font-size:14.5px;line-height:26px;color:#3a3126;text-align:justify}

/* testimonials */
.testi h2{position:absolute;left:111px;top:1870px;width:460px;font-size:34px;line-height:48px;font-weight:400}
.card{position:absolute;left:177px;top:1999px;width:846px;height:299px;border-radius:16px;background:var(--card);text-align:center}
.card .name{margin-top:56px;font-size:17px;color:#333}
.card blockquote{margin:18px auto 0;width:720px;font-size:28px;line-height:48px;color:#2a2a2a}
.arrow{position:absolute;width:58px;height:58px;border-radius:50%;display:flex;align-items:center;justify-content:center}
.dot{position:absolute;top:2350px;width:8px;height:8px;border-radius:50%;background:#ccc}

/* quote */
.quote{top:2478px;left:0;width:1200px;height:574px;background:linear-gradient(180deg,#ececec 0%,#e4e8ee 55%,#d9dee6 100%)}
.quote h2{position:absolute;left:0;width:1200px;top:68px;text-align:center;font-size:34px;font-weight:400}
.field{position:absolute;background:var(--white);border-radius:4px;box-shadow:0 2px 8px rgba(0,0,0,.06);font-size:13px;color:#555;padding:24px 22px}

/* faq */
.faq-photo{left:0;top:3231px;width:605px;height:502px;background:linear-gradient(160deg,#ffffff 0%,#dfe6f2 35%,#2f5fb8 60%,#1b3e8a 100%);
  clip-path:polygon(20% 0,80% 0,100% 100%,0 100%,0 50%)}
.faq h2{position:absolute;left:541px;top:3143px;width:480px;font-size:31px;line-height:44px;font-weight:400}
.qa{position:absolute;left:543px;width:511px;background:var(--white);box-shadow:0 2px 10px rgba(0,0,0,.09);padding:0 24px}
.qa .q{display:flex;justify-content:space-between;align-items:center;height:60px;font-size:15px;color:#222;font-weight:500}
.qa .q span:last-child{color:#777;font-size:20px}
.qa .a{font-size:11px;line-height:19px;color:#777;margin-top:-8px}

/* footer */
.footer{left:0;top:3733px;width:1200px;height:365px;background:var(--black);border-top:7px solid var(--green-dark);
  border-left:7px solid var(--green-dark);border-right:7px solid var(--green-dark);border-radius:190px 190px 0 0/150px 150px 0 0}
.footer .brand{left:108px;top:108px;font-size:40px;color:var(--white)}
.social{position:absolute;top:3961px;width:44px;height:44px;border-radius:50%;border:2px solid var(--white)}
.fcol{position:absolute;top:3826px;color:var(--white)}
.fcol h4{font-size:19px;font-weight:600;letter-spacing:.3px;margin-bottom:18px}
.fcol a{display:block;color:var(--white);text-decoration:none;font-size:15px;line-height:25.5px}
.fcol .c{display:flex;gap:12px;font-size:15px;line-height:25px;margin-bottom:12px}
.copy{position:absolute;left:0;width:1200px;top:4050px;text-align:center;color:var(--white);font-size:14px}
</style>
</head>
<body>

<header class="abs topbar">
  <div class="item" style="left:111px">
    <svg width="18" height="22" viewBox="0 0 18 22" fill="none" stroke="#444" stroke-width="1.6"><path d="M9 21s7-7 7-12A7 7 0 0 0 2 9c0 5 7 12 7 12z"/><circle cx="9" cy="9" r="2.6"/></svg>
    <span>Lorem ipsum dolor sit</span>
  </div>
  <div class="item" style="left:906px">
    <svg width="22" height="22" viewBox="0 0 24 24" fill="none" stroke="#444" stroke-width="1.6"><path d="M5 3h4l2 5-3 2a12 12 0 0 0 6 6l2-3 5 2v4a2 2 0 0 1-2 2A18 18 0 0 1 3 5a2 2 0 0 1 2-2z"/></svg>
    <span>+1 (888) 888 8888</span>
  </div>
</header>

<nav class="abs nav">
  <div class="brand">VoltaNix</div>
  <a style="left:387px">Home</a>
  <a style="left:466px">About Us</a>
  <a style="left:568px">Products</a>
  <a style="left:668px">Services</a>
  <a style="left:764px">Blog</a>
  <a style="left:832px">Contact Us</a>
  <div class="btn" style="left:950px;top:24px;width:139px;height:46px">Get a Quote</div>
</nav>

<section class="abs hero" role="img" aria-label="Modern dark house with solar roof panels at dusk, washed with a green overlay">
  <h1 class="display">Power Life on Your Terms</h1>
  <p>Lorem ipsum dolor sit amet, consectetur adipiscing elit, sed do eiusmod tempor incididunt ut labore et dolore magna aliqua.</p>
  <div class="btn" style="left:111px;top:301px;width:140px;height:46px">Get Started</div>
</section>

<section class="services">
  <h2 class="display">Our Services</h2>
  <div class="svc" style="left:111px">
    <svg width="50" height="40" viewBox="0 0 50 40" fill="none" stroke="#222" stroke-width="1.6"><path d="M3 18 22 4l19 14"/><path d="M8 15v22h28V15"/><path d="M19 37V26h8v11"/><path d="M24 10h22l-5 8"/><rect x="10" y="20" width="6" height="6"/><rect x="30" y="20" width="6" height="6"/></svg>
    <h3>Home solar and battery experience</h3>
    <p>Lorem ipsum dolor sit amet, consectetur adipiscing elit, sed do eiusmod tempor incididunt ut labore et dolore magna aliqua.</p>
  </div>
  <div class="divider" style="left:422px"></div>
  <div class="svc" style="left:466px">
    <svg width="46" height="44" viewBox="0 0 46 44" fill="none" stroke="#222" stroke-width="1.6"><rect x="4" y="14" width="14" height="28"/><rect x="18" y="6" width="14" height="36"/><rect x="32" y="18" width="10" height="24"/><path d="M8 20h6M8 26h6M8 32h6M22 12h6M22 18h6M22 24h6M22 30h6M35 24h4M35 30h4M25 2v4"/></svg>
    <h3>Smart technology</h3>
    <p>Lorem ipsum dolor sit amet, consectetur adipiscing elit, sed do eiusmod tempor incididunt ut labore et dolore magna aliqua.</p>
  </div>
  <div class="divider" style="left:766px"></div>
  <div class="svc" style="left:820px">
    <svg width="46" height="44" viewBox="0 0 46 44" fill="none" stroke="#222" stroke-width="1.6"><path d="M26 6 16 24h9l-4 16 12-20h-9l4-14z"/><path d="M8 8l4 4M38 8l-4 4M4 22h5M37 22h5M23 1v3" stroke-dasharray="2 2"/></svg>
    <h3>The VoltaNix</h3>
    <p>Lorem ipsum dolor sit amet, consectetur adipiscing elit, sed do eiusmod tempor incididunt ut labore et dolore magna aliqua.</p>
  </div>
</section>

<section class="abs about" role="img" aria-label="Technician in a hard hat installing solar panels on a roof at sunset">
  <h2 class="display">About VoltaNix</h2>
  <p>Sed ut perspiciatis unde omnis iste natus error sit voluptatem accusantium doloremque laudantium, totam rem aperiam, eaque ipsa quae ab illo inventore veritatis et quasi architecto beatae vitae dicta sunt explicabo. Nemo enim ipsam voluptatem quia voluptas sit aspernatur aut odit aut fugit, sed quia consequuntur magni dolores eos qui ratione voluptatem sequi nesciunt. Neque porro quisquam est, qui dolorem ipsum quia dolor sit amet, consectetur, adipisci velit, sed quia non numquam eius modi tempora incidunt ut labore et dolore magnam aliquam quaerat voluptatem.</p>
  <div class="btn" style="left:610px;top:387px;width:141px;height:46px">Learn More</div>
</section>

<section class="testi">
  <h2 class="display">What Our Client Says</h2>
  <div class="card">
    <div class="name">John Smith</div>
    <blockquote>"Lorem ipsum dolor sit amet, consectetur adipiscing elit, sed do eiusmod tempor incididunt ut labore et dolore magna aliqua.”</blockquote>
  </div>
  <div class="arrow" style="left:464px;top:2325px;border:1px solid #e6e6e6">
    <svg width="24" height="16" viewBox="0 0 24 16" fill="none" stroke="#ccc" stroke-width="1.8"><path d="M23 8H2M8 2 2 8l6 6"/></svg>
  </div>
  <div class="dot" style="left:556px;background:#222"></div>
  <div class="dot" style="left:583px"></div>
  <div class="dot" style="left:609px"></div>
  <div class="dot" style="left:634px"></div>
  <div class="arrow" style="left:679px;top:2325px;border:2px solid #222">
    <svg width="24" height="16" viewBox="0 0 24 16" fill="none" stroke="#222" stroke-width="1.8"><path d="M1 8h21M16 2l6 6-6 6"/></svg>
  </div>
</section>

<section class="abs quote" role="img" aria-label="Soft faded field of solar panels under a pale sky">
  <h2 class="display">Get a Free Personalized Quote</h2>
  <div class="field" style="left:204px;top:162px;width:383px;height:62px">Name</div>
  <div class="field" style="left:611px;top:162px;width:384px;height:62px">Phone Number</div>
  <div class="field" style="left:204px;top:247px;width:383px;height:62px">Email</div>
  <div class="field" style="left:611px;top:247px;width:384px;height:62px">Zip Code</div>
  <div class="field" style="left:204px;top:329px;width:791px;height:97px">Message</div>
  <div class="btn" style="left:536px;top:454px;width:126px;height:46px">Submit</div>
</section>

<section class="faq">
  <div class="abs faq-photo" role="img" aria-label="Worker in blue overalls and hard hat drilling on solar panels"></div>
  <h2 class="display">Frequently Asked Questions</h2>
  <div class="qa" style="top:3247px;height:60px"><div class="q"><span>Lorem ipsum dolor sit amet, consectetur</span><span>+</span></div></div>
  <div class="qa" style="top:3325px;height:122px"><div class="q"><span>Sed ut perspiciatis unde omnis iste natus error</span><span style="color:#222">–</span></div>
    <div class="a">Neque porro quisquam est, qui dolorem ipsum quia dolor sit amet, consectetur, adipisci velit, sed quia non numquam eius modi tempora incidun</div></div>
  <div class="qa" style="top:3463px;height:60px"><div class="q"><span>Ut enim ad minima veniam, quis nostrum</span><span>+</span></div></div>
  <div class="qa" style="top:3540px;height:60px"><div class="q"><span>Quis autem vel eum iure reprehenderit qui in ea</span><span>+</span></div></div>
  <div class="btn" style="left:727px;top:3640px;width:142px;height:44px">Load More</div>
</section>

<footer class="abs footer">
  <div class="brand">VoltaNix</div>
</footer>
<div class="social" style="left:113px"></div>
<div class="social" style="left:172px;background:var(--green);border-color:var(--green)"></div>
<div class="social" style="left:233px"></div>
<div class="social" style="left:293px"></div>

<div class="fcol" style="left:393px">
  <h4>QUICK LINKS</h4>
  <a>Home</a><a>About Us</a><a>Products</a><a>Services</a><a>Blog</a><a>Contact Us</a>
</div>
<div class="fcol" style="left:582px;width:200px">
  <h4>CONTACT US</h4>
  <div class="c"><svg width="16" height="20" viewBox="0 0 18 22" fill="#fff" style="flex:none;margin-top:4px"><path d="M9 21s7-7 7-12A7 7 0 0 0 2 9c0 5 7 12 7 12zm0-9a3 3 0 1 1 0-6 3 3 0 0 1 0 6z"/></svg><span>Lorem ipsum dolor sit amet, consectetur</span></div>
  <div class="c"><svg width="16" height="16" viewBox="0 0 24 24" fill="#fff" style="flex:none;margin-top:4px"><path d="M5 3h4l2 5-3 2a12 12 0 0 0 6 6l2-3 5 2v4a2 2 0 0 1-2 2A18 18 0 0 1 3 5a2 2 0 0 1 2-2z"/></svg><span>+1 (888) 888 8888</span></div>
  <div class="c"><svg width="16" height="14" viewBox="0 0 24 18" fill="#fff" style="flex:none;margin-top:6px"><path d="M0 2 12 10 24 2V0H0zM0 5v13h24V5l-12 8z"/></svg><span>info@VoltaNix.com</span></div>
</div>
<div class="fcol" style="left:826px">
  <h4>SIGN UP FOR NEWSLETTER</h4>
  <div style="display:flex;width:236px;height:44px;margin-top:4px">
    <div style="flex:1;background:#fff;color:#888;font-size:14px;padding:13px 12px;border-radius:3px 0 0 3px">Email Address</div>
    <div style="width:56px;background:var(--green);display:flex;align-items:center;justify-content:center;border-radius:0 3px 3px 0">
      <svg width="18" height="14" viewBox="0 0 24 18" fill="#fff"><path d="M0 2 12 10 24 2V0H0zM0 5v13h24V5l-12 8z"/></svg>
    </div>
  </div>
</div>
<div class="copy">©Copyrights 2024 VoltaNix &nbsp; | &nbsp; All Rights Reserved</div>

</body>
</html>
```